My project benefits Military, First Responders, Police, Fire, and Educators.

Contact Information for Business Card

2 Sided appointment card. Visual side will have my head shot with "Brisk Lantern" in a bold graffic/text. I am picturing maybe the headshot applied to a filter that has a matrix effect where the picture is made up of data/numbers flowing vertically through the photo. I am of course open to other concepts as well. Side two will have contact info presented in an attractive visual complimenting the front.

```html
<!DOCTYPE html>
<html lang="en">
<head>
<meta charset="utf-8">
<title>Brisk Lantern – Business Card</title>
<link href="https://fonts.googleapis.com/css2?family=Open+Sans:wght@300;400;600&display=swap" rel="stylesheet">
<style>
  :root {
    --page-bg: #3a3230;
    --card-black: #0c0c0c;
    --card-edge: #1a1a1a;
    --accent-green: #1fb083;
    --text-white: #f2f2f2;
    --logo-silver: #d4d4d4;
    --photo-dark: #1b2233;
    --photo-mid: #4a5670;
  }
  * { margin: 0; padding: 0; box-sizing: border-box; }
  html, body {
    width: 1200px; height: 900px; overflow: hidden;
    background: var(--page-bg);
    font-family: "Open Sans", Arial, sans-serif;
  }
  .canvas {
    position: relative; width: 1200px; height: 900px;
    display: flex; align-items: center; justify-content: center; gap: 50px;
  }
  .card {
    position: relative; width: 520px; height: 300px;
    background: var(--card-black);
    border: 1px solid var(--card-edge);
    box-shadow: 0 18px 40px rgba(0,0,0,.55);
    overflow: hidden;
  }
  /* Contact side */
  .headshot {
    position: absolute; left: 0; bottom: 0; width: 250px; height: 280px;
    background: linear-gradient(160deg, var(--photo-mid) 0%, var(--photo-dark) 70%, var(--card-black) 100%);
    border-top-right-radius: 120px 140px;
  }
  .divider {
    position: absolute; left: 262px; top: 70px; width: 1px; height: 110px;
    background: linear-gradient(to bottom, transparent, var(--accent-green), transparent);
  }
  .details { position: absolute; left: 282px; top: 62px; color: var(--text-white); }
  .person-name { color: var(--accent-green); font-weight: 600; font-size: 17px; line-height: 1.2; }
  .person-role { font-size: 13px; margin-bottom: 18px; }
  .contact-list { list-style: none; font-size: 13px; line-height: 1.6; }
  .contact-list li { display: flex; align-items: center; gap: 9px; }
  .contact-list svg { width: 11px; height: 11px; fill: var(--accent-green); flex: none; }
  /* Brand side */
  .brand-side { display: flex; flex-direction: column; align-items: center; justify-content: center; gap: 22px; }
  .brand-mark {
    width: 78px; height: 78px; border-radius: 50%;
    border: 4px solid var(--logo-silver);
  }
  .brand-name {
    color: var(--logo-silver); font-weight: 300; font-size: 34px; letter-spacing: 2px;
    text-transform: uppercase;
  }
</style>
</head>
<body>
<main class="canvas">
  <section class="card contact-side">
    <div class="headshot" role="img" aria-label="Head-and-shoulders portrait of the card holder in a navy suit and striped tie"></div>
    <div class="divider"></div>
    <div class="details">
      <p class="person-name">Daniel Mercer</p>
      <p class="person-role">Managing Director</p>
      <ul class="contact-list">
        <li><svg viewBox="0 0 24 24"><path d="M6.6 10.8a15.1 15.1 0 006.6 6.6l2.2-2.2c.3-.3.7-.4 1-.2 1.1.4 2.3.6 3.6.6.6 0 1 .4 1 1V20c0 .6-.4 1-1 1A17 17 0 013 4c0-.6.4-1 1-1h3.5c.6 0 1 .4 1 1 0 1.3.2 2.5.6 3.6.1.3 0 .7-.2 1z"/></svg>044-555 019 342</li>
        <li><svg viewBox="0 0 24 24"><path d="M2 5h20v14H2z M2 5l10 8 10-8" /></svg>info@brisklantern.com</li>
        <li><svg viewBox="0 0 24 24"><circle cx="12" cy="12" r="10"/></svg>www.brisklantern.com</li>
      </ul>
    </div>
  </section>
  <section class="card brand-side">
    <div class="brand-mark"></div>
    <p class="brand-name">Brisk Lantern</p>
  </section>
</main>
</body>
</html>
```